New Business Cards for NYC Salon

We are updating all of our cards. 7142-8863-2095 is my account number. We put names of our stylists on their cards. The back should include appointment space. Were looking for something more sleek and modern. Black/White Silver... or even touches of the orange color on our website which has been our thing for years. The design should communicate professional upscale boutique salon for men and women. Should be able to incorporate design into thank you cards, referral cards, brochure and postcards. The file is a zip file...we like the stacked ones black or white or the side versions.

Industry/Entity Type

Beauty Salon

Contact Information for Business Card

Marcus Elling's Salon313 W. 53rd Street, New York NY 10019 212-683-2741 info@marcusellingsalon.example www.marcusellingsalon.example

Font styles to use
Other font styles liked:
• trajan

Requirements
Must have
• we print a different card for every person in the salon. Begin by designing with the name Marcus. We will change it with every employee when printing. Must have a space for appointment date and time.
Nice to have
• Were looking to move towards the stacked or side placed logo but not opposed to utilizing the circular.
Should not have
• Photos

```html
<!DOCTYPE html>
<html lang="en">
<head>
<meta charset="utf-8">
<title>Marcus Elling's Salon — Business Card</title>
<link rel="stylesheet" href="https://fonts.googleapis.com/css2?family=Cinzel:wght@400&family=Open+Sans:wght@400;600&display=swap">
<style>
  :root {
    --silver: #b8bbbf;
    --silver-light: #d4d6d9;
    --orange: #e8782a;
    --charcoal: #232325;
    --paper: #ffffff;
    --backdrop: #e7e7e9;
    --ink: #2e2e30;
    --muted: #6a6a6c;
    --rule: #9a9ca0;
  }
  * { box-sizing: border-box; margin: 0; padding: 0; }
  html, body { width: 1200px; height: 944px; overflow: hidden; }
  body {
    background: var(--backdrop);
    font-family: "Open Sans", Arial, sans-serif;
    color: var(--ink);
    position: relative;
  }
  .card {
    position: absolute;
    left: 250px;
    width: 700px;
    height: 400px;
    background: var(--paper);
    box-shadow: 0 6px 18px rgba(0,0,0,0.12);
    overflow: hidden;
  }
  .card--front { top: 40px; }
  .card--back { top: 504px; }
  .card__bands { position: absolute; inset: 0; width: 100%; height: 100%; }

  .wordmark {
    position: absolute;
    display: flex;
    align-items: center;
    gap: 14px;
  }
  .wordmark__dot {
    width: 16px; height: 16px;
    border-radius: 50%;
    background: var(--orange);
    flex: none;
  }
  .wordmark__name {
    font-family: "Cinzel", "Trajan Pro", serif;
    font-weight: 400;
    color: var(--ink);
    letter-spacing: 0.28em;
    line-height: 1.35;
    text-align: center;
  }
  .card--front .wordmark { left: 196px; top: 118px; }
  .card--front .wordmark__name { font-size: 24px; }
  .card--back .wordmark { left: 50px; top: 150px; }
  .card--back .wordmark__name { font-size: 15px; }

  .staff-tab {
    position: absolute;
    right: 24px; top: 52px;
    color: var(--paper);
    font-size: 17px;
    line-height: 24px;
  }
  .contact {
    position: absolute;
    left: 378px; top: 105px;
  }
  .contact__salon {
    font-size: 24px;
    font-weight: 400;
    color: var(--orange);
    letter-spacing: -0.01em;
    line-height: 1.3;
  }
  .contact__salon span { color: var(--charcoal); }
  .contact__address { font-size: 11.5px; color: var(--muted); margin-bottom: 16px; }
  .contact__line { font-size: 11.5px; color: var(--muted); line-height: 1.55; }
  .contact__line--gap { margin-top: 14px; }

  .appointment {
    position: absolute;
    left: 50px; top: 218px;
    width: 290px;
  }
  .appointment__title {
    font-size: 10.5px;
    font-weight: 600;
    letter-spacing: 0.18em;
    text-transform: uppercase;
    color: var(--orange);
    margin-bottom: 12px;
  }
  .appointment__row {
    display: flex;
    gap: 18px;
  }
  .appointment__field {
    flex: 1;
    display: flex;
    align-items: flex-end;
    gap: 8px;
    font-size: 11px;
    color: var(--muted);
  }
  .appointment__line {
    flex: 1;
    height: 16px;
    border-bottom: 1px solid var(--rule);
  }
</style>
</head>
<body>

<section class="card card--front" aria-label="Card front">
  <svg class="card__bands" viewBox="0 0 700 400" aria-hidden="true">
    <rect x="520" y="238" width="180" height="30" fill="var(--charcoal)"/>
    <rect x="0" y="318" width="200" height="30" fill="var(--charcoal)"/>
    <path d="M0 268 H170 C200 268 200 222 235 222 H500 C535 222 540 268 575 268 H700 V318 H0 Z" fill="var(--silver)"/>
    <rect x="0" y="314" width="700" height="4" fill="var(--orange)"/>
  </svg>
  <div class="wordmark">
    <span class="wordmark__dot"></span>
    <span class="wordmark__name">Marcus Elling's<br>Salon</span>
  </div>
</section>

<section class="card card--back" aria-label="Card back">
  <svg class="card__bands" viewBox="0 0 700 400" aria-hidden="true">
    <rect x="0" y="0" width="700" height="42" fill="var(--silver)"/>
    <rect x="560" y="0" width="140" height="14" fill="var(--charcoal)"/>
    <path d="M440 42 C462 42 462 86 490 86 H700 V42 Z" fill="var(--charcoal)"/>
    <rect x="0" y="300" width="700" height="10" fill="var(--orange)"/>
    <rect x="0" y="310" width="700" height="40" fill="var(--charcoal)"/>
  </svg>
  <div class="staff-tab">Marcus Elling</div>
  <div class="wordmark">
    <span class="wordmark__dot"></span>
    <span class="wordmark__name">Marcus Elling's<br>Salon</span>
  </div>
  <div class="appointment">
    <p class="appointment__title">Your Next Appointment</p>
    <div class="appointment__row">
      <div class="appointment__field">Date <span class="appointment__line"></span></div>
      <div class="appointment__field">Time <span class="appointment__line"></span></div>
    </div>
  </div>
  <div class="contact">
    <h1 class="contact__salon">MARCUS ELLING'S <span>SALON</span></h1>
    <p class="contact__address">742 E. 18th Street, New York NY 10003</p>
    <p class="contact__line">212-683-2741</p>
    <p class="contact__line contact__line--gap">info@marcusellingsalon.example</p>
    <p class="contact__line">www.marcusellingsalon.example</p>
  </div>
</section>

</body>
</html>
```